Corvanth Veylor - Advanced Skincare and undetectable Makeup for Men

We are in need of a professional webpage for our company Corvanth Veylor. We help every man feel his best by looking his best. Inspired by the myth of Corvanth, we offer makeup and skincare products along with education upon their use. Our mission is to celebrate masculinity in all of its forms, regardless of age, race, sexual orientation, or assigned gender at birth.

The webpage would serve as our online store, as a place where our clients can learn about our brand, view our "How-to" video tutorials, and get product information. An online blog will also be hosted in order to keep clients up to date with news, updates, media mentions, etc.

The color schemes that we use are mostly Black and Gold, with Red accents. please keep in mind that this is a men's cosmetics line, and therefore should read powerful, sexy, confident and bold - all with a high end look and feel.

Think along the lines of brands like Lem Brisko, QDV, Belluti, etc.

our logo is included in the files attached. images and copy will be added in at a later time; hence, general images that fit the feel and filler text is encouraged.

The products to be sold include:
a face cleanser in a pump dispenser bottle (1 size)
a mask in a round jar container (1 size)
a moisturizer in a pump container 1 size)
a concealer in a click pen with a brush applicator (3 shades)
a liquid liner pen (4 shades)
a contouring palette (2 shade options)
a setting spray (single option)

Target Market(s)

Millennial Men

Industry/Entity Type

Beauty

Number of Pages Required

5+ page

Font styles to use
Serif

Colors
ec1f27
000000
faa54b

Requirements
Must have
• ur essential requirements are:
• 1) a stunning and engaging landing page that truly captures the ideals of sexuality, boldness and confidence.
• 2) an interactive and engaging online store that is easy to update / add product / information to.
• 3) Product pages supporting various toggling images of the product, a shade selection option, ingredient information, usage instructions, pricing, and a link to a "how to video" unique to each individual product.
• 4) dedicated space where all of the tutorials can be organized together
• 5) an organized Blog section, that would include a segment for a Q&A section for us to update as the brand grows, ongoing contests (that would be easily hidden if there are no contests running at the moment) as well as general news and updates segment.
• 6) an "about us" page, where our customers are able to learn about our story, inspirations, humanitarian efforts and philosophies in product contents and purity.
• 7) a contact us page, which would include social media links, contact email and telephone number as well as physical address to be updated upon launch.
• 8) discrete privacy policy, terms of use, and return policy links available at the bottom of every page
Nice to have
• 1) A posting forum where clients could post their looks using our products, or maybe a live stream of our Pictoval account.
• 2) a member sign in page so that we can collect and store customer information for faster check out, keep track of purchases attached to their email address (future loyalty program plans) and maintain an email database for email notifications and the such.

```html
<!DOCTYPE html>
<html lang="en">
<head>
<meta charset="utf-8">
<title>Corvanth Veylor — Skincare and Makeup for Men</title>
<link href="https://fonts.googleapis.com/css2?family=Merriweather:wght@700;900&family=Lato:ital,wght@0,400;0,700;0,900;1,400&display=swap" rel="stylesheet">
<style>
:root{
  --orange:#f7a043;
  --orange-dark:#e8892b;
  --black:#0b0b0b;
  --ink:#222;
  --muted:#7a7a7a;
  --line:#dcdcdc;
  --soft:#f3f3f3;
  --white:#fff;
  --skin:#d9b49a;
  --skin-shadow:#9c7358;
}
*{box-sizing:border-box;margin:0;padding:0}
html,body{width:1200px;height:3672px;overflow:hidden}
body{position:relative;background:var(--white);font-family:'Lato',sans-serif;color:var(--ink)}
.abs{position:absolute}
.serif{font-family:'Merriweather',serif}
.accent{color:var(--orange)}
.btn{position:absolute;display:flex;align-items:center;justify-content:center;background:var(--orange);color:var(--black);font-weight:700;font-size:15px;border-radius:8px;height:40px}
.section-title{position:absolute;left:0;width:1200px;text-align:center;font-family:'Merriweather',serif;font-weight:900;font-size:26px;color:var(--black);text-transform:uppercase;letter-spacing:.5px}
.section-title::after{content:"";display:block;width:56px;height:2px;background:var(--orange);margin:12px auto 0}

/* header */
.site-header{left:0;top:0;width:1200px;height:112px;background:var(--white)}
.social{display:flex;gap:14px}
.social span{width:14px;height:14px;border-radius:50%;background:var(--black)}
.nav a{position:absolute;top:46px;font-size:15px;color:var(--orange);text-decoration:none}
.brand{position:absolute;left:450px;top:22px;width:300px;text-align:center}
.brand .mark{width:34px;height:34px;background:var(--black);margin:0 auto 10px}
.brand .name{font-family:'Merriweather',serif;font-weight:900;font-size:15px;letter-spacing:5px;color:var(--black)}

/* hero */
.hero{left:0;top:112px;width:1200px;height:580px;overflow:hidden}
.hero-photo{position:absolute;inset:0;background:
  radial-gradient(ellipse 260px 330px at 930px 230px,#e3bda2 0%,#cf9f80 45%,rgba(207,159,128,0) 100%),
  radial-gradient(ellipse 220px 160px at 1010px 520px,#c89576 0%,rgba(200,149,118,0) 100%),
  radial-gradient(ellipse 110px 190px at 690px 420px,#1c1c1c 0%,#3c3c3c 55%,rgba(60,60,60,0) 100%),
  radial-gradient(ellipse 70px 140px at 810px 450px,#2a2a2a 0%,rgba(42,42,42,0) 100%),
  linear-gradient(100deg,#2f2f2f 0%,#5e5e5e 25%,#a9a39c 50%,#ddd3c9 70%,#e9e1d8 100%)}
.hero-title{left:80px;top:160px;font-family:'Merriweather',serif;font-weight:900;font-size:26px;color:var(--orange);letter-spacing:1px}
.hero-tag{left:80px;top:210px;width:320px;font-style:italic;font-size:14px;line-height:1.5;color:#f5f5f5}

/* welcome */
.welcome-text{left:250px;top:860px;width:700px;text-align:center;font-size:14px;line-height:1.75;color:var(--muted)}

/* products */
.products{left:0;top:1120px;width:1200px;height:780px;background:var(--soft)}
.card{position:absolute;background:var(--white);border:1px solid var(--line)}
.card.feature{border:2px solid var(--orange)}
.card .badge{position:absolute;right:0;top:0;width:46px;height:46px}
.card .shot{position:absolute;border-radius:6px}
.card h3{position:absolute;font-size:14px;font-weight:700;line-height:1.35;color:var(--black)}
.card .price{position:absolute;font-size:14px;color:var(--orange)}
.card .cart-btn{position:absolute;width:108px;height:34px;border:1px solid var(--line);border-radius:18px;font-size:13px;font-weight:700;display:flex;align-items:center;justify-content:center;background:var(--white)}

/* blog */
.post{position:absolute;top:2012px;width:320px;height:300px;border-radius:4px;overflow:hidden}
.post .shot{position:absolute;inset:0}
.post .shade{position:absolute;left:0;right:0;bottom:0;height:130px;background:linear-gradient(to top,rgba(0,0,0,.9),rgba(0,0,0,0))}
.post .date{position:absolute;left:22px;bottom:70px;font-size:12px;color:#ddd}
.post .title{position:absolute;left:22px;bottom:22px;width:270px;font-size:15px;font-weight:700;line-height:1.35;color:var(--white)}

/* testimonial */
.testimonial{left:0;top:2368px;width:1200px;height:420px;background:var(--soft)}
.quote-text{left:448px;top:168px;width:620px;font-size:14px;line-height:1.7;color:var(--muted)}
.dots{left:560px;top:322px;display:flex;gap:10px}
.dots span{width:9px;height:9px;border-radius:50%;background:#9aa}
.dots span.on{background:#334}

/* contact */
.contact-title{left:80px;top:2860px;font-family:'Merriweather',serif;font-weight:900;font-size:24px;color:var(--black)}
.contact-title::after{content:"";display:block;width:50px;height:2px;background:var(--orange);margin-top:10px}
.field{position:absolute;border:1px solid var(--line);font-size:12px;color:var(--orange);padding:12px 10px;background:var(--white)}
.info{position:absolute;left:780px;display:flex;align-items:center;gap:20px;font-size:13px;color:var(--muted);line-height:1.5}
.info .ico{width:44px;height:44px;border-radius:50%;background:var(--orange);display:flex;align-items:center;justify-content:center;flex:none}

/* footer */
.site-footer{left:0;top:3230px;width:1200px;height:442px}
.foot-links{left:0;top:3490px;width:1200px;display:flex;justify-content:center;gap:22px;font-size:15px;color:var(--black)}
.foot-links i{font-style:normal;color:#555}
.foot-social{left:0;top:3535px;width:1200px;display:flex;justify-content:center;gap:12px}
.foot-social span{width:26px;height:26px;border-radius:50%;background:var(--black)}
.copyright{left:0;top:3610px;width:1200px;height:62px;background:var(--white);display:flex;align-items:center;justify-content:center;font-size:13px;font-weight:700;color:var(--black)}
</style>
</head>
<body>

<header class="site-header abs">
  <div class="social abs" style="left:70px;top:48px"><span></span><span></span><span></span><span></span></div>
  <nav class="nav">
    <a style="left:262px">About Us</a>
    <a style="left:370px">Products</a>
    <a style="left:760px">Blog</a>
    <a style="left:846px">Contact Us</a>
  </nav>
  <div class="brand"><div class="mark"></div><div class="name">CORVANTH VEYLOR</div></div>
  <svg class="abs" style="left:1078px;top:40px" width="34" height="30" viewBox="0 0 34 30" aria-label="Cart">
    <path d="M2 4h5l4 14h15l4-10H9" fill="none" stroke="#111" stroke-width="2.4" stroke-linejoin="round"/>
    <circle cx="13" cy="24" r="2.4" fill="#111"/><circle cx="24" cy="24" r="2.4" fill="#111"/>
    <circle cx="28" cy="6" r="6" fill="#f7a043"/>
  </svg>
</header>

<section class="hero abs">
  <div class="hero-photo" role="img" aria-label="Man applying face cream beside a row of grooming product bottles"></div>
  <div class="hero-title abs">CORVANTH VEYLOR</div>
  <p class="hero-tag abs">Lorem ipsum is simply dummy text of the printing and typesetting industry. Lorem Ipsum has been</p>
  <div class="btn" style="left:80px;top:278px;width:118px">Contact Us</div>
  <svg class="abs" style="left:0;top:470px" width="1200" height="110" viewBox="0 0 1200 110" preserveAspectRatio="none">
    <polygon points="0,110 0,96 1200,20 1200,110" fill="#0b0b0b"/>
    <polygon points="0,110 0,102 1200,34 1200,30 0,96" fill="#f7a043"/>
    <polygon points="0,110 1200,64 1200,110" fill="#ffffff"/>
  </svg>
</section>

<h2 class="section-title" style="top:776px">Welcome to <span class="accent">Corvanth Veylor</span></h2>
<p class="welcome-text abs">Lorem Ipsum is simply dummy text of the printing and typesetting industry. Lorem Ipsum has been the industry's standard dummy text ever since the 1500s, when an unknown printer took a galley of type and scrambled it to make a type specimen book. It has survived not only five centuries, but also the leap into electronic typesetting, remaining essentially unchanged. It was popularised in the 1960s with containing Lorem Ipsum passages.</p>
<div class="btn" style="left:530px;top:1004px;width:140px">Know More</div>

<section class="products abs">
  <h2 class="section-title" style="top:56px">Our <span class="accent">Products</span></h2>
</section>

<div class="card feature" style="left:80px;top:1240px;width:322px;height:510px">
  <svg class="badge" viewBox="0 0 46 46"><polygon points="0,0 46,0 46,46" fill="#f7a043"/><ellipse cx="32" cy="13" rx="7" ry="4.5" fill="none" stroke="#111" stroke-width="1.6"/><circle cx="32" cy="13" r="1.8" fill="#111"/></svg>
  <div class="shot" role="img" aria-label="Face cleanser in an amber pump dispenser bottle" style="left:85px;top:30px;width:150px;height:265px;background:radial-gradient(ellipse 60px 110px at 50% 62%,#e2ad55 0%,#b97c25 60%,rgba(185,124,37,0) 100%),radial-gradient(ellipse 30px 40px at 50% 12%,#2a2a2a 0%,rgba(42,42,42,0) 100%),#fbf6ef"></div>
  <h3 style="left:40px;top:320px;width:240px;text-align:center">A face cleanser in a pump dispenser bottle</h3>
  <div class="price" style="left:0;top:372px;width:318px;text-align:center">Price: 65.00</div>
  <div class="cart-btn" style="left:105px;top:404px">Add to Cart</div>
</div>

<div class="card" style="left:440px;top:1240px;width:322px;height:240px">
  <svg class="badge" viewBox="0 0 46 46"><polygon points="0,0 46,0 46,46" fill="#f7a043"/><ellipse cx="32" cy="13" rx="7" ry="4.5" fill="none" stroke="#111" stroke-width="1.6"/><circle cx="32" cy="13" r="1.8" fill="#111"/></svg>
  <div class="shot" role="img" aria-label="Mask in a round glass jar" style="left:25px;top:35px;width:115px;height:140px;background:radial-gradient(ellipse 48px 55px at 50% 58%,#e9ecee 0%,#c9ced2 65%,rgba(201,206,210,0) 100%),radial-gradient(ellipse 42px 14px at 50% 22%,#b9bdc1 0%,rgba(185,189,193,0) 100%),#fafafa"></div>
  <h3 style="left:160px;top:42px;width:140px">A mask in a round jar container</h3>
  <div class="price" style="left:160px;top:100px">Price: 125.00</div>
  <div class="cart-btn" style="left:160px;top:136px">Add to Cart</div>
</div>

<div class="card" style="left:800px;top:1240px;width:322px;height:240px">
  <svg class="badge" viewBox="0 0 46 46"><polygon points="0,0 46,0 46,46" fill="#f7a043"/><ellipse cx="32" cy="13" rx="7" ry="4.5" fill="none" stroke="#111" stroke-width="1.6"/><circle cx="32" cy="13" r="1.8" fill="#111"/></svg>
  <div class="shot" role="img" aria-label="Black setting spray bottle" style="left:30px;top:35px;width:100px;height:140px;background:radial-gradient(ellipse 26px 62px at 50% 55%,#1a1a1a 0%,#3b3b3b 70%,rgba(59,59,59,0) 100%),radial-gradient(ellipse 14px 10px at 50% 60%,#c5306a 0%,rgba(197,48,106,0) 100%),#fafafa"></div>
  <h3 style="left:160px;top:42px;width:140px">A setting spray</h3>
  <div class="price" style="left:160px;top:80px">Price: 30.00</div>
  <div class="cart-btn" style="left:160px;top:116px">Add to Cart</div>
</div>

<div class="card" style="left:440px;top:1510px;width:322px;height:240px">
  <svg class="badge" viewBox="0 0 46 46"><polygon points="0,0 46,0 46,46" fill="#f7a043"/><ellipse cx="32" cy="13" rx="7" ry="4.5" fill="none" stroke="#111" stroke-width="1.6"/><circle cx="32" cy="13" r="1.8" fill="#111"/></svg>
  <div class="shot" role="img" aria-label="Set of clear moisturizer pump containers" style="left:25px;top:35px;width:120px;height:150px;background:radial-gradient(ellipse 55px 60px at 50% 60%,#dfe3e7 0%,#bfc5cb 60%,rgba(191,197,203,0) 100%),radial-gradient(ellipse 50px 20px at 50% 20%,#a9afb5 0%,rgba(169,175,181,0) 100%),#fafafa"></div>
  <h3 style="left:160px;top:42px;width:140px">A moisturizer in a pump container</h3>
  <div class="price" style="left:160px;top:100px">Price: 45.00</div>
  <div class="cart-btn" style="left:160px;top:136px">Add to Cart</div>
</div>

<div class="card" style="left:800px;top:1510px;width:322px;height:240px">
  <svg class="badge" viewBox="0 0 46 46"><polygon points="0,0 46,0 46,46" fill="#f7a043"/><ellipse cx="32" cy="13" rx="7" ry="4.5" fill="none" stroke="#111" stroke-width="1.6"/><circle cx="32" cy="13" r="1.8" fill="#111"/></svg>
  <div class="shot" role="img" aria-label="Silver liquid liner pen" style="left:30px;top:35px;width:100px;height:150px;background:radial-gradient(ellipse 16px 68px at 50% 50%,#4a4a4a 0%,#9a9a9a 55%,rgba(154,154,154,0) 100%),#fafafa"></div>
  <h3 style="left:160px;top:42px;width:140px">A liquid liner pen</h3>
  <div class="price" style="left:160px;top:80px">Price: 55.00</div>
  <div class="cart-btn" style="left:160px;top:116px">Add to Cart</div>
</div>

<div class="btn" style="left:505px;top:1786px;width:190px">View All products</div>

<h2 class="section-title" style="top:1942px">Latest <span class="accent">Blog</span></h2>
<article class="post" style="left:80px">
  <div class="shot" role="img" aria-label="Portrait of a man touching his jaw" style="background:radial-gradient(ellipse 110px 140px at 55% 40%,#c29a80 0%,#8c6a55 50%,rgba(140,106,85,0) 100%),radial-gradient(ellipse 120px 70px at 55% 12%,#2b211c 0%,rgba(43,33,28,0) 100%),linear-gradient(135deg,#e6e6e6,#9a9a9a 60%,#3a3a3a)"></div>
  <div class="shade"></div><div class="date">25 October, 2018</div>
  <div class="title">Lorem ipsum is simply dummy text of the printing</div>
</article>
<article class="post" style="left:440px">
  <div class="shot" role="img" aria-label="Black and white portrait of a bearded man" style="background:radial-gradient(ellipse 100px 130px at 50% 42%,#bdbdbd 0%,#7a7a7a 55%,rgba(122,122,122,0) 100%),radial-gradient(ellipse 110px 60px at 50% 10%,#1d1d1d 0%,rgba(29,29,29,0) 100%),linear-gradient(135deg,#f2f2f2,#a6a6a6 55%,#2e2e2e)"></div>
  <div class="shade"></div><div class="date">12 February, 2018</div>
  <div class="title">Lorem ipsum is simply dummy text of the printing</div>
</article>
<article class="post" style="left:800px">
  <div class="shot" role="img" aria-label="Man applying skincare cream" style="background:radial-gradient(ellipse 120px 120px at 60% 45%,#d2a786 0%,#a87a5c 55%,rgba(168,122,92,0) 100%),radial-gradient(ellipse 60px 40px at 80% 25%,#f1e4d6 0%,rgba(241,228,214,0) 100%),linear-gradient(135deg,#f1ebe4,#bda38c 55%,#4a3a2e)"></div>
  <div class="shade"></div><div class="date">15 November, 2018</div>
  <div class="title">Lorem ipsum is simply dummy text of the printing</div>
</article>

<section class="testimonial abs">
  <h2 class="section-title" style="top:60px">Client <span class="accent">Testimonial</span></h2>
  <div class="abs" role="img" aria-label="Client portrait photo" style="left:262px;top:150px;width:138px;height:150px;background:radial-gradient(ellipse 45px 55px at 50% 48%,#c9a88f 0%,#9d8070 60%,rgba(157,128,112,0) 100%),radial-gradient(ellipse 50px 25px at 50% 18%,#2a2420 0%,rgba(42,36,32,0) 100%),linear-gradient(160deg,#ececec,#a9a9a9);border:6px solid #fff;transform:rotate(-4deg);box-shadow:0 4px 10px rgba(0,0,0,.15)"></div>
  <div class="abs serif accent" style="left:448px;top:124px;font-size:44px;line-height:1">&ldquo;</div>
  <p class="quote-text abs">Lorem Ipsum is simply dummy text of the printing and typesetting industry. Lorem Ipsum has been the industry's standard dummy text ever since the 1500s, when an unknown printer took a galley of type and scrambled it to make a type specimen book.</p>
  <div class="abs accent" style="left:448px;top:278px;font-size:13px">— Client Name</div>
  <div class="dots abs"><span class="on"></span><span></span><span></span><span></span></div>
</section>

<h2 class="contact-title abs">GET <span class="accent">IN TOUCH</span></h2>
<div class="field" style="left:80px;top:2928px;width:320px;height:42px">Name*</div>
<div class="field" style="left:408px;top:2928px;width:332px;height:42px">E-mail*</div>
<div class="field" style="left:80px;top:2992px;width:320px;height:42px">Phone*</div>
<div class="field" style="left:408px;top:2992px;width:332px;height:42px">Subject</div>
<div class="field" style="left:80px;top:3056px;width:660px;height:96px">Message</div>
<div class="btn" style="left:80px;top:3168px;width:124px">Know More</div>

<div class="info" style="top:2920px">
  <div class="ico"><svg width="18" height="22" viewBox="0 0 18 22"><path d="M9 21s7-7 7-12A7 7 0 0 0 2 9c0 5 7 12 7 12z" fill="#111"/><circle cx="9" cy="9" r="2.6" fill="#f7a043"/></svg></div>
  <div>48 Marlow Lane, Suite 12,<br>Veylor City</div>
</div>
<div class="info" style="top:2988px">
  <div class="ico"><svg width="20" height="20" viewBox="0 0 20 20"><path d="M4 1l4 4-2 3c1 2 3 4 6 6l3-2 4 4-3 3C8 19 1 12 1 4z" fill="#111"/></svg></div>
  <div>555 018 2746</div>
</div>
<div class="info" style="top:3050px">
  <div class="ico"><svg width="20" height="16" viewBox="0 0 20 16"><rect x="1" y="1" width="18" height="14" rx="1" fill="#111"/><path d="M1 2l9 7 9-7" fill="none" stroke="#f7a043" stroke-width="1.6"/></svg></div>
  <div>info@corvanthveylor.com</div>
</div>

<footer class="site-footer abs">
  <svg class="abs" style="left:0;top:0" width="1200" height="442" viewBox="0 0 1200 442" preserveAspectRatio="none">
    <polygon points="0,70 1200,0 1200,442 0,442" fill="#0b0b0b"/>
    <polygon points="0,86 1200,28 1200,442 0,442" fill="#f7a043"/>
  </svg>
  <div class="brand" style="top:120px"><div class="mark"></div><div class="name">CORVANTH VEYLOR</div></div>
</footer>
<div class="foot-links abs"><span>About Us</span><i>|</i><span>Products</span><i>|</i><span>Blog</span><i>|</i><span>Contact Us</span></div>
<div class="foot-social abs"><span></span><span></span><span></span><span></span></div>
<div class="copyright abs">© CORVANTH VEYLOR - 2018. All Rights Reserved.</div>

</body>
</html>
```